Dietitian needs awesome business card

I need a contemporary design that's eye catching but professional.
My card is to given to doctors, specialists and patients alike.
I manage patients with chronic diseases
I have uploaded my logo and current business card, I would also like the other Certified Clinical Nutritionist logo incorporated into the design

Target Market(s)

Doctors, specialists and patients

Industry/Entity Type

Healthcare

Contact Information for Business Card

www.brightfieldnutrition.com.au
Ph: 0427 561 903
Fax: 6457 2183
email: marcus.k.diet@fernmail.com
Space on the back of the card with: Appointment date, Appointment time and appointment location

Font styles to use
Serif

Colors
fbee3e
876aae
ffc214

Requirements
Must have
• My Logo
• Certified Clinical Nutritionist Logo
• My 4 locations - Pinebrook Medical Centre, North Corrin Health, Hollis Medical, Ashcombe Doctors Surgery
Nice to have
• I like the colours in my current business card

```html
<!DOCTYPE html>
<html lang="en">
<head>
<meta charset="utf-8">
<title>Brightfield Nutrition &amp; Dietetics – Business Card</title>
<link href="https://fonts.googleapis.com/css2?family=Jost:wght@400;500&display=swap" rel="stylesheet">
<style>
  :root {
    --stage: #e4e4e4;
    --card-white: #ffffff;
    --leaf-green: #afc741;
    --deep-navy: #1d2a86;
    --royal-blue: #2357b5;
    --rule-grey: #9a9a9a;
    --mist: #eef2ea;
  }
  * { box-sizing: border-box; margin: 0; padding: 0; }
  html, body { width: 1200px; height: 886px; overflow: hidden; }
  body {
    background: var(--stage);
    font-family: "Jost", sans-serif;
    position: relative;
  }
  .card {
    position: absolute;
    top: 288px;
    width: 540px;
    height: 310px;
    border-radius: 18px;
    overflow: hidden;
    box-shadow: 0 6px 18px rgba(0,0,0,.18);
  }
  /* Back: appointment card */
  .card--appointment { left: 40px; background: var(--card-white); }
  .appointment__backdrop {
    position: absolute; inset: 0;
    background: radial-gradient(ellipse at 60% 45%, var(--mist) 0%, #f7f9f5 45%, var(--card-white) 80%);
  }
  .brand {
    position: absolute; top: 30px; right: 34px;
    display: flex; align-items: center; gap: 8px;
    color: var(--deep-navy); font-size: 17px; font-weight: 500;
  }
  .brand__dot { width: 18px; height: 18px; border-radius: 50%; background: var(--royal-blue); }
  .write-line {
    position: absolute; left: 40px; right: 40px; height: 1px; background: var(--rule-grey);
  }
  .field {
    position: absolute; top: 178px; display: flex; align-items: flex-end;
    color: var(--deep-navy); font-size: 16px; font-weight: 500;
  }
  .field__rule { height: 1px; background: var(--rule-grey); margin-left: 8px; margin-bottom: 4px; }
  .field__suffix { font-size: 12px; margin-left: 4px; }
  .locations {
    position: absolute; top: 214px; list-style: none;
    color: var(--deep-navy); font-size: 14px; line-height: 22px;
  }
  .locations li { display: flex; align-items: center; gap: 8px; }
  .locations li::before {
    content: ""; width: 12px; height: 12px; border: 1.5px solid var(--deep-navy);
  }
  /* Front: contact card */
  .card--contact { left: 620px; background: var(--leaf-green); }
  .contact__artwork {
    position: absolute; left: -40px; top: 10px; width: 360px; height: 320px;
    background: radial-gradient(closest-side at 50% 50%, var(--royal-blue) 0%, #2a4fa8 55%, rgba(42,79,168,.45) 80%, rgba(42,79,168,0) 100%);
  }
  .contact {
    position: absolute; right: 34px; top: 110px; text-align: right;
    color: #fff; font-size: 16px; line-height: 22px;
  }
  .contact__name { color: var(--deep-navy); font-size: 27px; font-weight: 500; line-height: 32px; }
  .contact__role { font-size: 18px; margin-bottom: 10px; }
  .contact__numbers { font-size: 18px; }
</style>
</head>
<body>

<section class="card card--appointment" aria-label="Appointment card">
  <div class="appointment__backdrop" role="img" aria-label="Faint photograph of fresh green vegetables"></div>
  <div class="brand"><span class="brand__dot"></span>Brightfield Nutrition &amp; Dietetics</div>
  <div class="write-line" style="top:86px"></div>
  <div class="write-line" style="top:120px"></div>
  <div class="write-line" style="top:154px"></div>
  <div class="field" style="left:40px">Date :<span class="field__rule" style="width:190px"></span></div>
  <div class="field" style="left:290px">Time :<span class="field__rule" style="width:130px"></span><span class="field__suffix">AM/PM</span></div>
  <ul class="locations" style="left:40px">
    <li>Pinebrook Medical Centre</li>
    <li>North Corrin Health</li>
  </ul>
  <ul class="locations" style="left:290px">
    <li>Ashcombe Doctors Surgery</li>
    <li>Hollis Medical</li>
  </ul>
</section>

<section class="card card--contact" aria-label="Contact card">
  <div class="contact__artwork" role="img" aria-label="Blue illustration of a stomach with a chef's knife"></div>
  <div class="contact">
    <p class="contact__name">Marcus Kellaway</p>
    <p class="contact__role">Nutritionist &amp; Chef</p>
    <p class="contact__numbers">0427 561 903</p>
    <p class="contact__numbers">6457 2183</p>
    <p>marcus.k.diet@fernmail.com</p>
    <p>brightfieldnutrition.com.au</p>
  </div>
</section>

</body>
</html>
```